Updated website design needed for Radiology Group, Pine Hollow Imaging Partners

Clean, uncluttered, updated design needed for top regional Radiology Center. Focus on personal, patient oriented design, (not clinical). Should be simple and easy to navigate, with clear CTAs. Use blues, greens and photos of people in the Central Oregon outdoors.
Uncoded, PSD design only. 2 pages: Home page and one example interior page.
reference current site: http://www.phipclinic-example.com/
Sites they like:
http://www.valescanlabs-example.com/
http://www.tbmx-example.net/handler.cfm?event=practice,main
http://www.kestrelbonecare-example.com/

Medical Imaging

2 page

Sans Serif

• Personal and patient friendly.
• Lots of white space, clean and uncluttered. Clear CTAs, such as: Patient Bill Pay, Make an Appointment, Meet Our Doctors
• Use copy and contact information from the current site.
• Use outdoor images from Central Oregon, late Winter/ Spring (snow, light colors, spring green, for example)
• Include one example interior page, either Your Exam or Meet Our Doctors
• The client likes:
• Meet Our Doctors slider section, and big, easy to navigate Information Center on www.kestrelbonecare-example.com
• The personal feel of the Your Exam section on www.valescanlabs-example.com
• Blues and Greens, outdoorsy imagery
• The client does not like:
• complex drop down menus
• clinical feel
• Do not use lorum ipsum or dummy text.
• Do not use outdoor images from other regions. Do not use Summer (hot, poolside) or Fall (red/orange leaves) images.

```html
<!DOCTYPE html>
<html lang="en">
<head>
<meta charset="utf-8">
<title>Meet Our Doctors – Pine Hollow Imaging Partners</title>
<link href="https://fonts.googleapis.com/css2?family=Open+Sans:wght@400;600&family=Raleway:wght@400&display=swap" rel="stylesheet">
<style>
:root{
  --blue:#2f92f5;
  --blue-light:#5bb6fb;
  --green:#42d86f;
  --name-blue:#3a8fe8;
  --text:#555;
  --text-dark:#222;
  --gray-bg:#f6f6f6;
  --rule:#e6e6e6;
  --photo-a:#5b6470;
  --photo-b:#2c3138;
}
*{box-sizing:border-box;margin:0;padding:0}
html,body{width:1070px;height:1200px;overflow:hidden;background:#fff}
body{font-family:"Open Sans",sans-serif;color:var(--text)}
.page{position:relative;width:1350px;height:1514px;transform:scale(.79259);transform-origin:0 0}
.abs{position:absolute}

/* header */
.brand{left:100px;top:11px;display:flex;align-items:center;gap:8px}
.brand-mark{width:46px;height:48px;background:#8a93c8}
.brand-name{font-size:13px;color:#333;line-height:1.15;width:90px}
.bill-pay{left:883px;top:29px;font-size:14px;color:#555}
.cta{left:1001px;top:17px;width:167px;height:41px;background:var(--green);color:#fff;font-size:14px;display:flex;align-items:center;justify-content:center}

/* nav */
.nav{left:0;top:71px;width:1350px;height:50px;background:var(--blue)}
.nav a{position:absolute;top:0;height:50px;line-height:52px;color:#fff;font-size:13.5px;text-decoration:none}
.nav .active{left:99px;width:101px;background:var(--green);text-align:center}

/* title band */
.title-band{left:0;top:121px;width:602px;height:97px;background:linear-gradient(180deg,var(--blue-light),var(--blue))}
.title-band h1{position:absolute;left:173px;top:28px;font-family:"Raleway",sans-serif;font-weight:400;font-size:30px;color:#fff}
.crumb-band{left:602px;top:121px;width:748px;height:97px;background:var(--gray-bg)}
.crumb{position:absolute;right:102px;top:40px;font-size:14px;color:#444}
.crumb span{margin:0 13px;color:#777}

/* doctors */
.doctor{width:570px;height:160px}
.doctor-photo{position:absolute;left:0;top:0;width:150px;height:150px;border-radius:50%;border:4px solid var(--blue);background:radial-gradient(circle at 50% 40%,var(--photo-a),var(--photo-b))}
.doctor-info{position:absolute;left:165px;top:-9px;width:410px}
.doctor-info h2{font-family:"Raleway",sans-serif;font-weight:400;font-size:21px;color:var(--name-blue);margin-bottom:4px}
.doctor-info p{font-size:12.3px;line-height:19.8px}
.doctor-info b{font-weight:600;color:var(--text-dark)}

.divider{left:57px;top:1181px;width:1293px;height:2px;background:var(--rule)}

/* footer */
.foot-brand{left:133px;top:1226px;display:flex;align-items:center;gap:8px}
.foot-about{left:133px;top:1287px;width:232px;font-size:13px;line-height:22px;color:#555}
.vrule{top:1220px;width:1px;height:185px;background:var(--rule)}
.foot-col h3{font-weight:400;font-size:20px;color:#333;margin-bottom:14px}
.foot-col ul{list-style:none}
.foot-col li{font-size:13px;color:#555;line-height:25px}
.foot-col li::before{content:"•";margin-right:6px;color:#333}
.contact li{display:flex;align-items:center;gap:9px;font-size:14px;line-height:33px;color:#555}
.contact li::before{content:none}
.contact a{color:var(--name-blue);text-decoration:none}
.bottom-bar{left:0;top:1461px;width:1350px;height:53px;background:var(--blue);color:#fff;font-size:14px;text-align:center;line-height:54px}
</style>
</head>
<body>
<div class="page">

  <header>
    <div class="brand abs"><div class="brand-mark"></div><div class="brand-name">Pine Hollow Imaging Partners</div></div>
    <div class="bill-pay abs">Patient Bill Pay</div>
    <div class="cta abs">Meet Our Doctors</div>
  </header>

  <nav class="nav abs">
    <a class="active">Home</a>
    <a style="left:238px">About Us</a>
    <a style="left:332px">Our Services</a>
    <a style="left:445px">For Patients</a>
    <a style="left:556px">Our Physicians</a>
    <a style="left:683px">For Physicians</a>
    <a style="left:807px">PACS &amp; Document</a>
    <a style="left:955px">Appointments</a>
    <a style="left:1083px">Our Locations</a>
  </nav>

  <div class="title-band abs"><h1>Meet Our Doctors</h1></div>
  <div class="crumb-band abs"><div class="crumb">Home<span>/</span>Meet Our Doctors</div></div>

  <main>
    <article class="doctor abs" style="left:99px;top:303px">
      <div class="doctor-photo" role="img" aria-label="Portrait photo of Dr. Adrian Keller"></div>
      <div class="doctor-info"><h2>Adrian Keller, M.D.</h2>
        <p><b>Specialty-</b> Neuroradiology, Diagnostic Radiology<br><b>Certification-</b> National Radiology Board 2012, and National Radiology Board of Radiology CAQ Neuroradiology 2014<br><b>Medical School-</b> Ridgefield State Medical School, 2007<br><b>Residency-</b> Ridgefield State Medical School, 2012<br><b>Fellowship-</b> Neuroradiology-Cascade Valley University, 2014</p></div>
    </article>
    <article class="doctor abs" style="left:693px;top:303px">
      <div class="doctor-photo" role="img" aria-label="Portrait photo of Dr. Marisa Dunlow-Hart"></div>
      <div class="doctor-info"><h2>Marisa Dunlow-Hart, M.D.</h2>
        <p><b>Specialty-</b> Neuroradiology, Diagnostic Radiology<br><b>Certification-</b> National Radiology Board 2012, and National Radiology Board of Radiology CAQ Neuroradiology 2014<br><b>Medical School-</b> Ridgefield State Medical School, 2007<br><b>Residency-</b> Ridgefield State Medical School, 2012<br><b>Fellowship-</b> Neuroradiology-Cascade Valley University, 2014</p></div>
    </article>
    <article class="doctor abs" style="left:99px;top:521px">
      <div class="doctor-photo" role="img" aria-label="Portrait photo of Dr. Owen Castell"></div>
      <div class="doctor-info"><h2>Owen Castell, M.D.</h2>
        <p><b>Specialty-</b> Neuroradiology, Diagnostic Radiology<br><b>Certification-</b> National Radiology Board 2012, and National Radiology Board of Radiology CAQ Neuroradiology 2014<br><b>Medical School-</b> Ridgefield State Medical School, 2007<br><b>Residency-</b> Ridgefield State Medical School, 2012<br><b>Fellowship-</b> Neuroradiology-Cascade Valley University, 2014</p></div>
    </article>
    <article class="doctor abs" style="left:693px;top:521px">
      <div class="doctor-photo" role="img" aria-label="Portrait photo of Dr. Gregory L. Shaw"></div>
      <div class="doctor-info"><h2>Gregory L. Shaw, M.D.</h2>
        <p><b>Specialty-</b> Neuroradiology, Diagnostic Radiology<br><b>Certification-</b> National Radiology Board 2012, and National Radiology Board of Radiology CAQ Neuroradiology 2014<br><b>Medical School-</b> Ridgefield State Medical School, 2007<br><b>Residency-</b> Ridgefield State Medical School, 2012<br><b>Fellowship-</b> Neuroradiology-Cascade Valley University, 2014</p></div>
    </article>
    <article class="doctor abs" style="left:99px;top:743px">
      <div class="doctor-photo" role="img" aria-label="Portrait photo of Dr. Daniel R. Whitcomb"></div>
      <div class="doctor-info"><h2>Daniel R. Whitcomb, M.D.</h2>
        <p><b>Specialty-</b> Neuroradiology, Diagnostic Radiology<br><b>Certification-</b> National Radiology Board 2012, and National Radiology Board of Radiology CAQ Neuroradiology 2014<br><b>Medical School-</b> Ridgefield State Medical School, 2007<br><b>Residency-</b> Ridgefield State Medical School, 2012<br><b>Fellowship-</b> Neuroradiology-Cascade Valley University, 2014</p></div>
    </article>
    <article class="doctor abs" style="left:693px;top:743px">
      <div class="doctor-photo" role="img" aria-label="Portrait photo of Dr. Stephen Maravel"></div>
      <div class="doctor-info"><h2>Stephen Maravel, M.D.</h2>
        <p><b>Specialty-</b> Neuroradiology, Diagnostic Radiology<br><b>Certification-</b> National Radiology Board 2012, and National Radiology Board of Radiology CAQ Neuroradiology 2014<br><b>Medical School-</b> Ridgefield State Medical School, 2007<br><b>Residency-</b> Ridgefield State Medical School, 2012<br><b>Fellowship-</b> Neuroradiology-Cascade Valley University, 2014</p></div>
    </article>
    <article class="doctor abs" style="left:99px;top:967px">
      <div class="doctor-photo" role="img" aria-label="Portrait photo of Dr. Martin J. Aldous"></div>
      <div class="doctor-info"><h2>Martin J. Aldous, M.D</h2>
        <p><b>Specialty-</b> Neuroradiology, Diagnostic Radiology<br><b>Certification-</b> National Radiology Board 2012, and National Radiology Board of Radiology CAQ Neuroradiology 2014<br><b>Medical School-</b> Ridgefield State Medical School, 2007<br><b>Residency-</b> Ridgefield State Medical School, 2012<br><b>Fellowship-</b> Neuroradiology-Cascade Valley University, 2014</p></div>
    </article>
    <article class="doctor abs" style="left:693px;top:967px">
      <div class="doctor-photo" role="img" aria-label="Portrait photo of Dr. Paul D. Henley"></div>
      <div class="doctor-info"><h2>Paul D. Henley, M.D.</h2>
        <p><b>Specialty-</b> Neuroradiology, Diagnostic Radiology<br><b>Certification-</b> National Radiology Board 2012, and National Radiology Board of Radiology CAQ Neuroradiology 2014<br><b>Medical School-</b> Ridgefield State Medical School, 2007<br><b>Residency-</b> Ridgefield State Medical School, 2012<br><b>Fellowship-</b> Neuroradiology-Cascade Valley University, 2014</p></div>
    </article>
  </main>

  <div class="divider abs"></div>

  <footer>
    <div class="foot-brand abs"><div class="brand-mark"></div><div class="brand-name">Pine Hollow Imaging Partners</div></div>
    <p class="foot-about abs">Pine Hollow Imaging Partners is a state-of-the-art Outpatient Imaging Center providing Professional Services to Central Oregon Hospitals and Clinics as well as providing services in its own outpatient clinic.</p>

    <div class="vrule abs" style="left:382px"></div>
    <div class="vrule abs" style="left:645px"></div>
    <div class="vrule abs" style="left:927px"></div>

    <div class="foot-col abs" style="left:411px;top:1219px">
      <h3>For Patients</h3>
      <ul><li>About Your Visit</li><li>Why Choose Us?</li><li>Patient Forms</li><li>Billing and Insurance</li><li>Locations and Maps</li><li>Appointments</li></ul>
    </div>
    <div class="foot-col abs" style="left:690px;top:1219px">
      <h3>Quick Links</h3>
      <ul style="margin-top:-4px"><li>Home</li><li>About Us</li><li>Our Physicians</li><li>For Physicians</li><li>Disclaimer</li><li>HIPAA</li><li>Log-In</li></ul>
    </div>
    <div class="foot-col contact abs" style="left:955px;top:1219px">
      <h3 style="margin-bottom:2px">Contact Us</h3>
      <ul>
        <li><svg width="16" height="16" viewBox="0 0 24 24"><path fill="#999" d="M6.6 10.8a15 15 0 0 0 6.6 6.6l2.2-2.2c.3-.3.7-.4 1-.2 1.1.4 2.3.6 3.6.6.6 0 1 .4 1 1V20c0 .6-.4 1-1 1A17 17 0 0 1 3 4c0-.6.4-1 1-1h3.5c.6 0 1 .4 1 1 0 1.3.2 2.5.6 3.6.1.3 0 .7-.2 1z"/></svg>(555) 010-6633 - <a>Main Line</a></li>
        <li><svg width="16" height="16" viewBox="0 0 24 24"><path fill="#999" d="M6.6 10.8a15 15 0 0 0 6.6 6.6l2.2-2.2c.3-.3.7-.4 1-.2 1.1.4 2.3.6 3.6.6.6 0 1 .4 1 1V20c0 .6-.4 1-1 1A17 17 0 0 1 3 4c0-.6.4-1 1-1h3.5c.6 0 1 .4 1 1 0 1.3.2 2.5.6 3.6.1.3 0 .7-.2 1z"/></svg>(555) 010-9383 - <a>Scheduling</a></li>
        <li><svg width="16" height="16" viewBox="0 0 24 24"><path fill="#999" d="M6.6 10.8a15 15 0 0 0 6.6 6.6l2.2-2.2c.3-.3.7-.4 1-.2 1.1.4 2.3.6 3.6.6.6 0 1 .4 1 1V20c0 .6-.4 1-1 1A17 17 0 0 1 3 4c0-.6.4-1 1-1h3.5c.6 0 1 .4 1 1 0 1.3.2 2.5.6 3.6.1.3 0 .7-.2 1z"/></svg>(555) 010-1614 - <a>Billing</a></li>
        <li><svg width="16" height="16" viewBox="0 0 24 24"><path fill="#999" d="M6.6 10.8a15 15 0 0 0 6.6 6.6l2.2-2.2c.3-.3.7-.4 1-.2 1.1.4 2.3.6 3.6.6.6 0 1 .4 1 1V20c0 .6-.4 1-1 1A17 17 0 0 1 3 4c0-.6.4-1 1-1h3.5c.6 0 1 .4 1 1 0 1.3.2 2.5.6 3.6.1.3 0 .7-.2 1z"/></svg>(555) 010-5977 - <a>Medical Records</a></li>
      </ul>
    </div>

    <div class="bottom-bar abs">Copyright 2016 Radiology. All right reserved.</div>
  </footer>
</div>
</body>
</html>
```